Design a Google site for a travel agency

I own a travel agency and I would like to have a Google site built for my company called Harborquestjourneys.com by Bright Path Holidays. Our specialty Cruising and adventure. We create a lot of custom tour of Europe and Peru. Our Adventure tours targets mainly women from 25 to 65. I would like to site especially the cruise to appeal to family but also upscale more expensive upscale clientele.
Updates

I would like to shift away from create a new site with multiple pages to one simple Google Site page with a Contact us page and testimonials. The sites theme is Cruise & Adventure Travel. We specialize in selling cruises and building custom travel tours around the world.

Target Market(s)

Cruisers and adventure travelers for women from 25 to 70

Industry/Entity Type

travel industry with a focus on cruising and adventure travel

Coding

Coded - Design and coding required

Number of Pages Required

5+ page

Font styles to use
Serif
Sans Serif

Requirements
Must have
• Home page, Cruise, Adventure Tours, Testimonials, About Us
Nice to have
• Auto place https://www.brightpathholidays.ca/offers into the site.
Should not have
• beach resorts

```html
<!DOCTYPE html>
<html lang="en">
<head>
<meta charset="utf-8">
<title>Bright Path Holidays — Book Unique Experiences</title>
<link href="https://fonts.googleapis.com/css2?family=Montserrat:wght@400;500&family=Quicksand:wght@500;600&family=Cormorant+Garamond:wght@500&display=swap" rel="stylesheet">
<style>
  :root {
    --sky-top: #b9cfe8;
    --sky-mid: #7d9fce;
    --sea-deep: #2f5fa3;
    --sea-light: #5aa7c4;
    --ink: #1f2d45;
    --white: #ffffff;
    --teal: #15a596;
    --chat: #5fc6aa;
    --nav-active: #e9e35a;
  }
  * { margin: 0; padding: 0; box-sizing: border-box; }
  html, body { width: 1200px; height: 517px; overflow: hidden; }
  body { font-family: "Quicksand", sans-serif; color: var(--white); }
  .page { position: relative; width: 1200px; height: 517px; overflow: hidden; }

  .hero-photo {
    position: absolute; inset: 0;
    background:
      linear-gradient(180deg, var(--sky-top) 0%, var(--sky-mid) 35%, #4d6f9e 45%, var(--sea-deep) 62%, var(--sea-light) 85%, #6fb6c6 100%);
  }

  .brand { position: absolute; left: 0; width: 1200px; top: 26px; text-align: center; }
  .brand-mark {
    display: inline-block; width: 30px; height: 30px; border-radius: 50%;
    border: 2px solid var(--white); vertical-align: middle;
  }
  .brand-name {
    display: block; margin-top: 6px;
    font-family: "Cormorant Garamond", serif; font-weight: 500;
    font-size: 15px; letter-spacing: 0.5px; color: var(--white);
  }

  .tagline { position: absolute; left: 0; width: 1194px; top: 94px; text-align: center; color: var(--ink); }
  .tagline h1 {
    font-family: "Montserrat", sans-serif; font-weight: 400;
    font-size: 23px; line-height: 26px; letter-spacing: 0.5px;
  }
  .tagline p { font-family: "Montserrat", sans-serif; font-size: 9.5px; margin-top: 5px; }

  .main-nav { position: absolute; left: 429px; top: 168px; display: flex; gap: 16px; font-size: 12.5px; font-weight: 500; }
  .main-nav a { color: var(--white); text-decoration: none; }
  .main-nav a.is-active { color: var(--nav-active); }

  .social-bar {
    position: absolute; left: 215px; top: 228px; width: 225px; height: 39px;
    border-top: 1px dashed var(--white); border-bottom: 1px dashed var(--white);
    display: flex; justify-content: center; align-items: center; gap: 22px;
  }
  .social-dot { width: 12px; height: 12px; border-radius: 50%; background: var(--white); }

  .search-icon { position: absolute; left: 300px; top: 290px; }
  .search-ribbon { position: absolute; left: 232px; top: 343px; }
  .search-ribbon span {
    position: absolute; left: 0; width: 200px; top: 11px; text-align: center;
    font-family: "Montserrat", sans-serif; font-size: 19px; letter-spacing: 6px; padding-left: 6px;
  }
  .search-note { position: absolute; left: 215px; width: 230px; top: 396px; text-align: center; font-size: 15px; font-weight: 500; }

  .welcome-button {
    position: absolute; left: 215px; top: 449px; width: 228px; height: 46px;
    border: 3px solid var(--white); display: flex; align-items: center; justify-content: center;
    font-family: "Montserrat", sans-serif; font-size: 13px; letter-spacing: 0.3px;
  }

  .offer-card {
    position: absolute; left: 484px; top: 228px; width: 501px; height: 271px;
    border: 4px solid var(--white); padding: 3px;
  }
  .offer-card-inner { width: 100%; height: 100%; border: 1px solid var(--white); position: relative; }
  .offer-title {
    position: absolute; left: 16px; top: 16px; right: 10px;
    font-family: "Montserrat", sans-serif; font-weight: 500;
    font-size: 40px; line-height: 38px; letter-spacing: -0.3px; text-transform: uppercase;
  }
  .offer-link {
    position: absolute; right: 11px; bottom: 13px; display: flex; align-items: center; gap: 20px;
    font-size: 15px; font-weight: 600; color: var(--white); text-decoration: none;
  }
  .offer-plus {
    width: 26px; height: 26px; border-radius: 50%; background: var(--teal);
    border: 2px solid var(--white); display: flex; align-items: center; justify-content: center;
    font-size: 15px; line-height: 1;
  }

  .chat-button {
    position: absolute; left: 1027px; top: 460px; width: 158px; height: 44px;
    background: var(--chat); border-radius: 4px; display: flex; align-items: center; justify-content: center;
    font-size: 14px; font-weight: 600;
  }
</style>
</head>
<body>
<div class="page">
  <div class="hero-photo" role="img" aria-label="Photo of green rocky islands in a blue sea under a cloudy sky, with a sailboat mast at the lower left"></div>

  <header class="brand">
    <span class="brand-mark"></span>
    <span class="brand-name">Bright Path Holidays</span>
  </header>

  <div class="tagline">
    <h1>BOOK UNIQUE<br>EXPERIENCES</h1>
    <p>Explore top rated itineraries around the world</p>
  </div>

  <nav class="main-nav">
    <a class="is-active" href="#">Home</a>
    <a href="#">About Us</a>
    <a href="#">Cruises</a>
    <a href="#">Packages</a>
    <a href="#">Adventure</a>
    <a href="#">Contest</a>
    <a href="#">Destinations</a>
    <a href="#">Vacations</a>
  </nav>

  <div class="social-bar" aria-label="Social links">
    <span class="social-dot"></span>
    <span class="social-dot"></span>
    <span class="social-dot"></span>
    <span class="social-dot"></span>
  </div>

  <svg class="search-icon" width="68" height="38" viewBox="0 0 68 38" aria-hidden="true">
    <g fill="none" stroke="#ffffff" stroke-width="2.5">
      <circle cx="15" cy="24" r="12"/>
      <circle cx="53" cy="24" r="12"/>
      <rect x="24" y="4" width="20" height="12" rx="4"/>
      <path d="M6 16 L16 4 L24 6 M62 16 L52 4 L44 6"/>
    </g>
  </svg>

  <div class="search-ribbon">
    <svg width="200" height="43" viewBox="0 0 200 43" aria-hidden="true">
      <polygon points="0,0 200,0 190,21.5 200,43 0,43 10,21.5" fill="#15a596"/>
    </svg>
    <span>SEARCH</span>
  </div>
  <p class="search-note">For A Holiday</p>

  <div class="welcome-button">WELCOME TO OUR WORLD</div>

  <section class="offer-card">
    <div class="offer-card-inner">
      <h2 class="offer-title">See how much you can save with these last minute Bright Path rates.</h2>
      <a class="offer-link" href="https://www.brightpathholidays.ca/offers">See Details <span class="offer-plus">+</span></a>
    </div>
  </section>

  <div class="chat-button">Let's Chat!</div>
</div>
</body>
</html>
```